Business card for my new company (Accounting firm)

I need a business card for my new business Brightwell Advisory and Ledger SA. Our services are accounting, tax, audit and financial management. Our customers are small companies, start-ups and new companies. The final design has to show financial security, trust and growth. Please find our logo attached to the business card. Text for the business card: Brightwell Advisory and Ledger SA Tomas Varenholt Director and Founder Certified Accountant Tel. 022 418 57 34 tv@clairevalconseil.ch www.clairevalconseil.ch Rue des Vergières 27 1201 Geneva
Target Market(s)
Our customers are small companies, start-ups and new companies.
Industry/Entity Type
Finance And Accounting
Contact Information for Business Card
Claireval Conseil et Comptes SA
Tomas Varenholt
Directeur et Fondateur
Expert-comptable diplômé
Tél. 022 418 57 34
tv@clairevalconseil.ch
www.clairevalconseil.ch
Rue des Vergières 27
1201 Genève

```html
<!DOCTYPE html>
<html lang="en">
<head>
<meta charset="utf-8">
<title>Claireval Conseil et Comptes SA – Business Card</title>
<link rel="stylesheet" href="https://fonts.googleapis.com/css2?family=Lato:ital,wght@0,400;0,700;0,900;1,400&display=swap">
<style>
  :root {
    --page-bg: #e9eaec;
    --blue-light: #2eb0e4;
    --blue-mid: #2294d2;
    --blue-deep: #1a6fb3;
    --navy: #16609f;
    --ink: #2f333a;
    --ink-soft: #4a4f57;
    --paper: #ffffff;
  }
  * { margin: 0; padding: 0; box-sizing: border-box; }
  html, body {
    width: 1200px; height: 1200px; overflow: hidden;
    background: var(--page-bg);
    font-family: "Lato", sans-serif;
  }
  .canvas {
    position: relative; width: 1200px; height: 1200px;
  }
  .card {
    position: absolute; left: 220px; width: 760px; height: 440px;
    box-shadow: 0 14px 30px rgba(0,0,0,0.18);
  }
  /* Front */
  .card-front {
    top: 130px;
    border-radius: 70px 0 70px 0;
    background: linear-gradient(180deg, var(--blue-mid) 0%, var(--blue-light) 40%, var(--blue-deep) 100%);
    display: flex; flex-direction: column; align-items: center; justify-content: center;
    color: var(--paper);
  }
  .front-brand {
    display: flex; align-items: center; gap: 16px;
    font-weight: 700; font-size: 46px; letter-spacing: 6px;
  }
  .front-brand .mark-dot {
    width: 22px; height: 22px; border-radius: 50%; background: var(--paper);
  }
  .front-web {
    margin-top: 40px; font-size: 20px; font-weight: 700; letter-spacing: 1.5px;
  }
  /* Back */
  .card-back {
    top: 630px;
    border-radius: 0 70px 0 70px;
    background: var(--paper);
    color: var(--ink);
  }
  .holder {
    position: absolute; left: 58px; top: 48px;
  }
  .holder-name {
    color: var(--navy); font-weight: 700; font-size: 24px; text-transform: uppercase;
  }
  .holder-role {
    font-size: 19px; color: var(--ink-soft); line-height: 1.2; margin-top: 2px;
  }
  .contact {
    position: absolute; left: 58px; bottom: 52px;
    list-style: none; font-size: 20px; line-height: 1.35;
  }
  .contact li { display: flex; align-items: center; gap: 10px; }
  .contact svg { width: 18px; height: 18px; fill: var(--ink-soft); }
  .contact .web { color: var(--blue-mid); }
  .contact .web svg { fill: var(--navy); }
  .brand {
    position: absolute; right: 60px; top: 120px; text-align: right;
    color: var(--ink); font-weight: 700;
  }
  .brand-name { font-size: 48px; letter-spacing: 5px; display: flex; align-items: center; justify-content: flex-end; gap: 14px; }
  .brand-name .mark-dot { width: 20px; height: 20px; background: var(--blue-mid); }
  .brand-sub { font-size: 15px; letter-spacing: 3.5px; margin-top: 4px; }
  .address {
    position: absolute; right: 60px; bottom: 52px; text-align: right;
    font-size: 21px; line-height: 1.3; color: var(--ink);
  }
</style>
</head>
<body>
<div class="canvas">
  <section class="card card-front">
    <div class="front-brand"><span class="mark-dot"></span>CLAIREVAL</div>
    <div class="front-web">www.clairevalconseil.ch</div>
  </section>

  <section class="card card-back">
    <div class="holder">
      <div class="holder-name">SA Tomas Varenholt</div>
      <div class="holder-role">Director and Founder<br>Certified Accountant</div>
    </div>

    <div class="brand">
      <div class="brand-name"><span class="mark-dot"></span>CLAIREVAL</div>
      <div class="brand-sub">CONSEIL ET COMPTES</div>
    </div>

    <ul class="contact">
      <li>
        <svg viewBox="0 0 24 24" aria-hidden="true"><path d="M6.6 10.8a15.1 15.1 0 0 0 6.6 6.6l2.2-2.2c.3-.3.7-.4 1-.2 1.1.4 2.3.6 3.6.6.6 0 1 .4 1 1V20c0 .6-.4 1-1 1A17 17 0 0 1 3 4c0-.6.4-1 1-1h3.5c.6 0 1 .4 1 1 0 1.3.2 2.5.6 3.6.1.3 0 .7-.2 1z"/></svg>
        022 418 57 34
      </li>
      <li>
        <svg viewBox="0 0 24 24" aria-hidden="true"><path d="M2 5h20v14H2zm2 2v.5l8 5 8-5V7l-8 5z"/></svg>
        tv@clairevalconseil.ch
      </li>
      <li class="web">
        <svg viewBox="0 0 24 24" aria-hidden="true"><path d="M12 2a10 10 0 1 0 0 20 10 10 0 0 0 0-20zm6.9 6h-3a15 15 0 0 0-1.3-3.9A8 8 0 0 1 18.9 8zM12 4c.8 1.2 1.5 2.5 1.9 4h-3.8c.4-1.5 1.1-2.8 1.9-4zM4.3 14a8 8 0 0 1 0-4h3.4a16 16 0 0 0 0 4zm.8 2h3a15 15 0 0 0 1.3 3.9A8 8 0 0 1 5.1 16zm3-8h-3a8 8 0 0 1 4.3-3.9C8.8 5.3 8.4 6.6 8.1 8zM12 20c-.8-1.2-1.5-2.5-1.9-4h3.8c-.4 1.5-1.1 2.8-1.9 4zm2.3-6H9.7a14 14 0 0 1 0-4h4.6a14 14 0 0 1 0 4zm.3 5.9c.6-1.2 1-2.5 1.3-3.9h3a8 8 0 0 1-4.3 3.9zm1.7-5.9a16 16 0 0 0 0-4h3.4a8 8 0 0 1 0 4z"/></svg>
        www.clairevalconseil.ch
      </li>
    </ul>

    <address class="address" style="font-style:normal">
      Rue des Vergières 27<br>1201 Geneva
    </address>
  </section>
</div>
</body>
</html>
```